Edit and Update existing catalog

I have a 60 paged catalog that needs to have some changes. We are adding around 20 pages, changing another 15 pages, and also have 10 pages that need to be graphically designed and inserted. The current existing catalog is included as well as a PDF explaining all the changes (Catalog Changes.pdf), as well as all the pages that need to be added and our logo.

Target Market(s)

physician offices and professional healthcare providers

Industry/Entity Type

Healthcare

Colors
0054AA
0677BA
7BADD7
CADEEF
E8F1F8

Requirements
Must have
• Additional pages must match the format of the existing catalog
Should not have
• No protected health information - all patient names, Date of births and accession #s should be removed, incase they are not please replace with XXX on the reports.

```html
<!DOCTYPE html>
<html lang="en">
<head>
<meta charset="utf-8">
<title>Lakeside Labs Catalog Spread</title>
<link href="https://fonts.googleapis.com/css2?family=Montserrat:wght@400;600;700;800&family=Open+Sans:wght@400;600;700&family=Tinos:wght@400;700&display=swap" rel="stylesheet">
<style>
:root{
  --navy:#0054AA;
  --blue:#0677BA;
  --sky:#7BADD7;
  --pale:#CADEEF;
  --mist:#E8F1F8;
  --tab:#2e2e30;
  --stage:#c9c9cb;
  --ink:#222;
  --rule:#9a9a9a;
  --red:#d0302a;
}
*{margin:0;padding:0;box-sizing:border-box}
html,body{width:720px;height:1200px;overflow:hidden;background:var(--stage)}
body{position:relative;font-family:"Open Sans",sans-serif;color:var(--ink)}
.page{position:absolute;width:156px;height:190px;background:#fff;overflow:hidden}
.tab{position:absolute;top:0;width:11px;height:100%;background:var(--tab);display:flex;align-items:center;justify-content:center}
.odd .tab{right:0}.even .tab{left:0}
.tab span{writing-mode:vertical-rl;color:#fff;font:600 2.7px "Open Sans",sans-serif;white-space:nowrap}
.pnum{position:absolute;bottom:3px;font-size:2.6px;color:#444}
.odd .pnum{right:15px}.even .pnum{left:15px}
.inner{position:absolute;top:8px;bottom:8px}
.odd .inner{left:8px;right:18px}.even .inner{left:19px;right:7px}
.brand{font:800 7px "Montserrat",sans-serif;color:var(--navy);letter-spacing:.2px;display:flex;align-items:center;gap:2px}
.brand i{display:inline-block;width:6px;height:6px;border:1px solid var(--navy);border-radius:50%}
.tiny{font-size:2.3px;line-height:3.1px}
.micro{font-size:1.9px;line-height:2.5px}
.intro .brand{justify-content:center;margin-top:26px;font-size:8px}
.clia{margin:3px auto 0;width:48px;border:.5px solid var(--navy);text-align:center;font:600 2.6px "Open Sans";color:var(--navy);padding:.5px 0}
.intro p{margin-top:8px;font-size:2.5px;line-height:3.4px}
.intro h4{margin:5px 0 1px 4px;font-size:2.6px}
.intro ul{margin-left:8px;font-size:2.4px;line-height:3.3px}
.addr{position:absolute;bottom:14px;left:0;right:0;display:flex;justify-content:space-around;font:600 2.2px "Montserrat";color:var(--blue);text-align:center}
.cover svg{position:absolute;inset:0}
.cover .brandmark{position:absolute;top:10px;left:8px;font:800 6px "Montserrat";color:#fff;display:flex;align-items:center;gap:2px}
.cover .brandmark i{width:7px;height:7px;border:1px solid #fff;border-radius:50%;display:inline-block}
.cover-title{position:absolute;font-family:"Montserrat",sans-serif;color:var(--blue);font-weight:800}
.vlabel{position:absolute;writing-mode:vertical-rl;font:600 2.6px "Open Sans";color:#fff}
.report{font-family:"Tinos",serif}
.rhead{display:flex;gap:4px;align-items:flex-start}
.rhead .brand{font-size:4.6px}
.rhead .brand i{width:4px;height:4px}
.final{position:absolute;top:0;right:0;font-size:2.3px;color:var(--red)}
.rule{border-top:.4px solid var(--rule);margin:2px 0}
.rtitle{font:700 3px "Tinos",serif;margin:2px 0 1px}
table{width:100%;border-collapse:collapse}
td,th{font-size:1.9px;line-height:2.6px;text-align:left;padding:0 .5px;white-space:nowrap}
th{border-bottom:.4px solid #555}
.boxed td{border:.3px solid #777}
.neg{color:var(--blue)}.pos{color:var(--red)}
.rfoot{position:absolute;bottom:0;left:0;right:0;font-size:1.9px;line-height:2.5px;display:flex;justify-content:space-between}
.vtitle{position:absolute;top:10px;bottom:10px;writing-mode:vertical-rl;transform:rotate(180deg);font:800 4.3px "Montserrat";color:var(--blue);text-align:center;letter-spacing:.3px}
.mtab th{background:var(--blue);color:#fff;font-size:1.8px}
.mtab .sec td{background:var(--blue);color:#fff;font-weight:700;text-align:center}
.mtab td{border-bottom:.25px solid var(--pale);font-size:1.7px;line-height:2.2px}
.formhead{background:var(--pale);padding:2px 3px;display:flex;justify-content:space-between;align-items:flex-end}
.formhead .brand{font-size:5px}
.formhead h3{font:800 3.6px "Montserrat";text-align:right;line-height:4px}
.formhead small{display:block;font-size:2.2px;font-weight:600}
.cols{display:grid;gap:2px;margin-top:2px}
.cols div{font-size:1.7px;line-height:2.3px}
.box{border:.4px solid #666;padding:1px}
.band{background:var(--blue);color:#fff;font:700 2.3px "Montserrat";text-align:center;padding:.5px 0;margin-top:2px}
.sub{font:700 2.2px "Montserrat";text-align:center;color:#333;margin-top:1px}
.sigs{display:flex;justify-content:space-between;font-size:2.2px;margin-top:4px}
.critical h2{font:800 3.8px "Montserrat";color:var(--blue);text-align:center;margin-top:3px;letter-spacing:.2px;white-space:nowrap}
.critical td{font-size:2.2px;line-height:3px;border-bottom:.3px solid var(--pale)}
.critical td+td{text-align:center}
</style>
</head>
<body>

<section class="page odd intro" style="left:21px;top:85px">
  <div class="tab"><span>Tabs Here - This portion will be trimmed off</span></div>
  <div class="inner">
    <div class="brand"><i></i>LAKESIDE LABS</div>
    <div class="clia">CLIA ID: 00D0000000</div>
    <p>Since 2017, Lakeside Labs has been dedicated to providing best-in-class patient care through cutting-edge technologies, rigorous quality control measures, comprehensive data analytics and reliable, timely results. Our commitment to state-of-the-art technology and research has allowed us to enhance the accuracy, speed and range of our services, strengthening our brand as the trusted laboratory partner in the medical community.</p>
    <h4>Why our clients use Lakeside Labs:</h4>
    <ul>
      <li>Local, MI based company</li>
      <li>Highest quality diagnostic equipment with accurate test results</li>
      <li>In-Network with EVERY MI based insurance carrier</li>
      <li>Low-cost billing for self-pay patients</li>
      <li>EMR integration with over 50 different systems and counting</li>
      <li>Industry leading turnaround time</li>
      <li>Comprehensive testing menu for both urine and oral fluid testing</li>
      <li>Innovative PCR testing covering a wide range of specialties</li>
      <li>Most advanced client web-portal with reporting and analysis</li>
      <li>Dedicated team of Pathologists available for consultation anytime</li>
      <li>4-hour STAT turnaround time</li>
      <li>Best-in-class customer service</li>
    </ul>
  </div>
  <div class="addr"><span>1450 MERIDIAN AVE, SUITE 210<br>FAIRVIEW, MI 48000</span><span>800 COMMERCE PLAZA, SUITE 400<br>FAIRVIEW, MI 48001</span></div>
  <div class="pnum">1</div>
</section>

<section class="page even" style="left:195px;top:85px">
  <div class="tab"><span>Tabs Here - This portion will be trimmed off</span></div>
  <div class="pnum">2</div>
</section>

<section class="page odd cover" style="left:369px;top:85px">
  <svg viewBox="0 0 156 190" aria-hidden="true">
    <polygon points="0,0 145,0 0,76" fill="#0054AA"/>
    <polygon points="0,76 145,0 145,4 0,82" fill="#2e2e30"/>
  </svg>
  <div role="img" aria-label="Photo of a physician and a smiling patient reviewing results on a tablet" style="position:absolute;left:0;right:11px;top:88px;bottom:0;background:linear-gradient(135deg,#dfe7ef,#a9b7c6 55%,#6d5a4e);clip-path:polygon(0 18%,100% 0,100% 100%,0 100%)"></div>
  <div class="brandmark"><i></i>LAKESIDE</div>
  <div class="cover-title" style="left:19px;top:70px;font-size:12px">Toxicology</div>
  <div style="position:absolute;left:20px;top:84px;font:600 2.8px Montserrat;letter-spacing:.2px">URINE AND ORAL FLUID DRUG TESTING</div>
  <div style="position:absolute;right:0;top:0;width:11px;height:100%;background:var(--blue)"></div>
  <div class="vlabel" style="right:3px;top:30px">Toxicology</div>
  <div class="vlabel" style="right:3px;top:100px;opacity:.6">Tab Area</div>
  <div class="pnum" style="color:#fff">3</div>
</section>

<section class="page even" style="left:542px;top:85px">
  <div class="tab"><span>Tabs Here - This portion will be trimmed off</span></div>
  <div class="pnum">4</div>
</section>

<section class="page odd report" style="left:21px;top:295px">
  <div class="tab"><span>Tabs Here - This portion will be trimmed off</span></div>
  <div class="inner">
    <div class="final">FINAL</div>
    <div class="rhead"><div class="brand"><i></i>LAKESIDE LABS</div><div class="micro">1450 Meridian Ave, Suite 210<br>(555) 014-2290<br>lakesidelabs.example</div><div class="micro">LAB DIRECTOR Daniel Reyes, MD<br>CLIA ID# 00D0000000</div></div>
    <div class="rule"></div>
    <div class="micro">XXX, XXX &nbsp; Patient #: XXX &nbsp; DOB: XXX &nbsp; Accession: XXX<br>Organization: Maple Care Clinic &nbsp; Collected: 11/18/2025</div>
    <div class="rtitle" style="text-align:center;text-decoration:underline">Drug Adherence Assessment Report</div>
    <div class="micro">Medications: Clonazepam, Trazodone &nbsp; Listed Medications Not Tested For: None</div>
    <div class="tiny" style="font-weight:700;margin-top:2px">PRESCRIBED MEDICATIONS</div>
    <table class="boxed"><tr><th>REPORTED</th><th>ANTICIPATED</th><th>RESULT</th><th>CUTOFF</th><th>OUTCOME</th><th>WINDOW</th></tr>
    <tr><td class="pos">Trazodone</td><td>Trazodone</td><td>&lt;25</td><td>25</td><td class="pos">NEGATIVE</td><td>2-3</td></tr>
    <tr><td class="pos">Clonazepam</td><td>7-Aminoclonazepam</td><td>&lt;25</td><td>25</td><td class="pos">NEGATIVE</td><td>2-3</td></tr></table>
    <div class="tiny" style="font-weight:700;margin-top:2px">INCONSISTENT RESULTS - ANALYTE DETECTED</div>
    <table class="boxed"><tr><th>ANALYTE</th><th>ILLICIT</th><th>RESULT</th><th>CUTOFF</th><th>OUTCOME</th><th>WINDOW</th></tr>
    <tr><td>Alpha-hydroxyalprazolam</td><td>No</td><td>382</td><td>25</td><td class="pos">POSITIVE</td><td>2-3</td></tr>
    <tr><td>O-desmethyltramadol</td><td>No</td><td>&gt;2500</td><td>25</td><td class="pos">POSITIVE</td><td>2-3</td></tr>
    <tr><td>Tramadol</td><td>No</td><td>&gt;2500</td><td>25</td><td class="pos">POSITIVE</td><td>2-4</td></tr></table>
    <div class="tiny" style="font-weight:700;margin-top:2px">SPECIMEN VALIDITY TESTING</div>
    <table class="boxed"><tr><th>TEST</th><th>RESULT</th><th>OUTCOME</th><th>RANGE</th></tr>
    <tr><td>Creatinine</td><td>23.68</td><td>Normal</td><td>20.00 - 400.00</td></tr>
    <tr><td>pH</td><td>7.36</td><td>Normal</td><td>4.50 - 9.00</td></tr>
    <tr><td>Specific Gravity</td><td>1.005</td><td>Normal</td><td>1.002 - 1.030</td></tr></table>
    <div class="tiny" style="font-weight:700;margin-top:2px">HISTORICAL REPORT</div>
    <table class="boxed"><tr><th>Analyte</th><th>10/1</th><th>11/1</th><th>12/1</th></tr>
    <tr><td>Alprazolam</td><td>44</td><td>72</td><td>61</td></tr>
    <tr><td>Buprenorphine</td><td>390</td><td>444</td><td>402</td></tr>
    <tr><td>Tramadol</td><td>&gt;2500</td><td>3000</td><td>2860</td></tr></table>
    <div class="rfoot"><span>Printed: 11/21/2025<br>Page: 1/3</span><span>STAT(S) Corrected (C) Amended (A)</span><span>Lab Results for: XXX</span></div>
  </div>
  <div class="pnum">5</div>
</section>

<section class="page even report" style="left:195px;top:295px">
  <div class="tab"><span>Tabs Here - This portion will be trimmed off</span></div>
  <div class="inner">
    <div class="final">FINAL</div>
    <div class="rhead"><div class="brand"><i></i>LAKESIDE LABS</div><div class="micro">1450 Meridian Ave, Suite 210<br>(555) 014-2290</div><div class="micro">LAB DIRECTOR Daniel Reyes, MD<br>CLIA ID# 00D0000000</div></div>
    <div class="rule"></div>
    <div class="micro">XXX, XXX &nbsp; Patient #: XXX &nbsp; DOB: XXX &nbsp; Accession: XXX</div>
    <div class="rtitle">LL Urine Confirmation</div>
    <table><tr><th>Test Name</th><th>Outcome</th><th>Result</th><th>Cutoff</th><th>Units</th><th>Status</th></tr>
    <tr><td><b>OPIATES &amp; OPIOIDS</b></td><td></td><td></td><td></td><td></td><td></td></tr>
    <tr><td>Buprenorphine</td><td class="neg">NEGATIVE</td><td></td><td>10</td><td>ng/mL</td><td>Consistent</td></tr>
    <tr><td>Norbuprenorphine</td><td class="neg">NEGATIVE</td><td></td><td>10</td><td>ng/mL</td><td>Consistent</td></tr>
    <tr><td>Carisoprodol</td><td class="neg">NEGATIVE</td><td></td><td>25</td><td>ng/mL</td><td>Consistent</td></tr>
    <tr><td>Codeine</td><td class="neg">NEGATIVE</td><td></td><td>25</td><td>ng/mL</td><td>Consistent</td></tr>
    <tr><td>Hydrocodone</td><td class="neg">NEGATIVE</td><td></td><td>25</td><td>ng/mL</td><td>Consistent</td></tr>
    <tr><td>Norhydrocodone</td><td class="neg">NEGATIVE</td><td></td><td>25</td><td>ng/mL</td><td>Consistent</td></tr>
    <tr><td>Morphine</td><td class="neg">NEGATIVE</td><td></td><td>25</td><td>ng/mL</td><td>Consistent</td></tr>
    <tr><td>Hydromorphone</td><td class="neg">NEGATIVE</td><td></td><td>25</td><td>ng/mL</td><td>Consistent</td></tr>
    <tr><td>Fentanyl</td><td class="neg">NEGATIVE</td><td></td><td>2.5</td><td>ng/mL</td><td>Consistent</td></tr>
    <tr><td>Norfentanyl</td><td class="neg">NEGATIVE</td><td></td><td>2.5</td><td>ng/mL</td><td>Consistent</td></tr>
    <tr><td>Meperidine</td><td class="neg">NEGATIVE</td><td></td><td>25</td><td>ng/mL</td><td>Consistent</td></tr>
    <tr><td>Normeperidine</td><td class="neg">NEGATIVE</td><td></td><td>25</td><td>ng/mL</td><td>Consistent</td></tr>
    <tr><td>Methadone</td><td class="neg">NEGATIVE</td><td></td><td>50</td><td>ng/mL</td><td>Consistent</td></tr>
    <tr><td>EDDP</td><td class="neg">NEGATIVE</td><td></td><td>50</td><td>ng/mL</td><td>Consistent</td></tr>
    <tr><td>Naloxone</td><td class="neg">NEGATIVE</td><td></td><td>25</td><td>ng/mL</td><td>Consistent</td></tr>
    <tr><td>Naltrexone</td><td class="neg">NEGATIVE</td><td></td><td>25</td><td>ng/mL</td><td>Consistent</td></tr>
    <tr><td>Oxycodone</td><td class="neg">NEGATIVE</td><td></td><td>25</td><td>ng/mL</td><td>Consistent</td></tr>
    <tr><td>Noroxycodone</td><td class="neg">NEGATIVE</td><td></td><td>25</td><td>ng/mL</td><td>Consistent</td></tr>
    <tr><td>Oxymorphone</td><td class="neg">NEGATIVE</td><td></td><td>25</td><td>ng/mL</td><td>Consistent</td></tr>
    <tr><td>Sufentanil</td><td class="neg">NEGATIVE</td><td></td><td>25</td><td>ng/mL</td><td>Consistent</td></tr>
    <tr><td>Tapentadol</td><td class="neg">NEGATIVE</td><td></td><td>25</td><td>ng/mL</td><td>Consistent</td></tr>
    <tr><td>Tramadol</td><td class="pos">POSITIVE</td><td>&gt;2500</td><td>25</td><td>ng/mL</td><td class="pos">Inconsistent</td></tr>
    <tr><td>O-desmethyltramadol</td><td class="pos">POSITIVE</td><td>&gt;2500</td><td>25</td><td>ng/mL</td><td class="pos">Inconsistent</td></tr></table>
    <div class="rfoot"><span>Printed: 11/21/2025<br>Page: 2/3</span><span>STAT(S) Corrected (C) Amended (A)</span><span>Lab Results for: XXX</span></div>
  </div>
  <div class="pnum">6</div>
</section>

<section class="page odd report" style="left:369px;top:295px">
  <div class="tab"><span>Tabs Here - This portion will be trimmed off</span></div>
  <div class="inner">
    <div class="final">FINAL</div>
    <div class="rhead"><div class="brand"><i></i>LAKESIDE LABS</div><div class="micro">1450 Meridian Ave, Suite 210<br>(555) 014-2290</div><div class="micro">LAB DIRECTOR Daniel Reyes, MD<br>CLIA ID# 00D0000000</div></div>
    <div class="rule"></div>
    <div class="micro">XXX, XXX &nbsp; Patient #: XXX &nbsp; DOB: XXX &nbsp; Accession: XXX</div>
    <div class="rtitle">LL Urine Confirmation</div>
    <table><tr><th>Test Name</th><th>Outcome</th><th>Result</th><th>Cutoff</th><th>Units</th><th>Status</th></tr>
    <tr><td><b>BENZODIAZEPINES</b></td><td></td><td></td><td></td><td></td><td></td></tr>
    <tr><td>Alprazolam</td><td class="neg">NEGATIVE</td><td></td><td>25</td><td>ng/mL</td><td>Consistent</td></tr>
    <tr><td>Alpha-hydroxyalprazolam</td><td class="pos">POSITIVE</td><td>382</td><td>25</td><td>ng/mL</td><td class="pos">Inconsistent</td></tr>
    <tr><td>Clonazepam</td><td class="neg">NEGATIVE</td><td></td><td>25</td><td>ng/mL</td><td class="pos">Inconsistent</td></tr>
    <tr><td>7-Aminoclonazepam</td><td class="neg">NEGATIVE</td><td></td><td>25</td><td>ng/mL</td><td class="pos">Inconsistent</td></tr>
    <tr><td>Diazepam</td><td class="neg">NEGATIVE</td><td></td><td>25</td><td>ng/mL</td><td>Consistent</td></tr>
    <tr><td>Nordiazepam</td><td class="neg">NEGATIVE</td><td></td><td>25</td><td>ng/mL</td><td>Consistent</td></tr>
    <tr><td>Temazepam</td><td class="neg">NEGATIVE</td><td></td><td>25</td><td>ng/mL</td><td>Consistent</td></tr>
    <tr><td>Oxazepam</td><td class="neg">NEGATIVE</td><td></td><td>25</td><td>ng/mL</td><td>Consistent</td></tr>
    <tr><td>Lorazepam</td><td class="neg">NEGATIVE</td><td></td><td>25</td><td>ng/mL</td><td>Consistent</td></tr>
    <tr><td>Trazodone</td><td class="neg">NEGATIVE</td><td></td><td>12.5</td><td>ng/mL</td><td class="pos">Inconsistent</td></tr>
    <tr><td><b>NEUROPATHIC ANALGESICS</b></td><td></td><td></td><td></td><td></td><td></td></tr>
    <tr><td>Gabapentin</td><td class="neg">NEGATIVE</td><td></td><td>1000</td><td>ng/mL</td><td>Consistent</td></tr>
    <tr><td>Pregabalin</td><td class="neg">NEGATIVE</td><td></td><td>1000</td><td>ng/mL</td><td>Consistent</td></tr>
    <tr><td><b>STIMULANTS</b></td><td></td><td></td><td></td><td></td><td></td></tr>
    <tr><td>Amphetamine</td><td class="neg">NEGATIVE</td><td></td><td>50</td><td>ng/mL</td><td>Consistent</td></tr>
    <tr><td>Methylphenidate</td><td class="neg">NEGATIVE</td><td></td><td>25</td><td>ng/mL</td><td>Consistent</td></tr>
    <tr><td>Phentermine</td><td class="neg">NEGATIVE</td><td></td><td>25</td><td>ng/mL</td><td>Consistent</td></tr>
    <tr><td><b>ILLICITS</b></td><td></td><td></td><td></td><td></td><td></td></tr>
    <tr><td>6-MAM</td><td class="neg">NEGATIVE</td><td></td><td>5</td><td>ng/mL</td><td>Consistent</td></tr>
    <tr><td>Cocaine</td><td class="neg">NEGATIVE</td><td></td><td>40</td><td>ng/mL</td><td>Consistent</td></tr>
    <tr><td>MDMA</td><td class="neg">NEGATIVE</td><td></td><td>50</td><td>ng/mL</td><td>Consistent</td></tr>
    <tr><td>THC-COOH</td><td class="neg">NEGATIVE</td><td></td><td>12.5</td><td>ng/mL</td><td>Consistent</td></tr></table>
    <div class="micro" style="margin-top:2px">* Any Toxicology Testing value that falls below the cutoff will be reported as NEGATIVE.</div>
    <div class="rfoot"><span>Printed: 11/21/2025<br>Page: 3/3</span><span>STAT(S) Corrected (C) Amended (A)</span><span>Lab Results for: XXX</span></div>
  </div>
  <div class="pnum">7</div>
</section>

<section class="page even" style="left:542px;top:295px">
  <div class="tab"><span>Tabs Here - This portion will be trimmed off</span></div>
  <div class="vtitle" style="left:13px">METABOLITES &amp; WINDOWS OF DETECTION</div>
  <div class="inner" style="left:26px">
    <table class="mtab">
      <tr><th>PARENT DRUG</th><th>Drug or metabolite detected</th><th>Window</th></tr>
      <tr class="sec"><td colspan="3">SYNTHETIC OPIOIDS</td></tr>
      <tr><td>Buprenorphine</td><td>Norbuprenorphine</td><td>2-3 days</td></tr>
      <tr><td>Fentanyl</td><td>Norfentanyl</td><td>2-3 days</td></tr>
      <tr><td>Meperidine</td><td>Normeperidine</td><td>2-3 days</td></tr>
      <tr><td>Methadone</td><td>EDDP</td><td>3-5 days</td></tr>
      <tr><td>Tapentadol</td><td>N-desmethyltapentadol</td><td>2-3 days</td></tr>
      <tr><td>Tramadol</td><td>O-desmethyltramadol</td><td>2-4 days</td></tr>
      <tr class="sec"><td colspan="3">BENZODIAZEPINES</td></tr>
      <tr><td>Alprazolam</td><td>Alpha-hydroxyalprazolam</td><td>2-3 days</td></tr>
      <tr><td>Clonazepam</td><td>7-Aminoclonazepam</td><td>2-3 days</td></tr>
      <tr><td>Diazepam</td><td>Nordiazepam, Oxazepam</td><td>5-7 days</td></tr>
      <tr><td>Lorazepam</td><td>Lorazepam glucuronide</td><td>2-4 days</td></tr>
      <tr><td>Temazepam</td><td>Oxazepam</td><td>2-4 days</td></tr>
      <tr class="sec"><td colspan="3">STIMULANTS</td></tr>
      <tr><td>Amphetamine</td><td>Amphetamine</td><td>2-3 days</td></tr>
      <tr><td>Methylphenidate</td><td>Ritalinic acid</td><td>1-2 days</td></tr>
      <tr><td>Phentermine</td><td>Phentermine</td><td>2-4 days</td></tr>
      <tr class="sec"><td colspan="3">ILLICITS</td></tr>
      <tr><td>Cocaine</td><td>Benzoylecgonine</td><td>2-4 days</td></tr>
      <tr><td>Heroin</td><td>6-MAM, Morphine</td><td>1 day</td></tr>
      <tr><td>Marijuana</td><td>THC-COOH</td><td>3-30 days</td></tr>
      <tr><td>MDMA</td><td>MDA</td><td>1-2 days</td></tr>
      <tr class="sec"><td colspan="3">OTHER</td></tr>
      <tr><td>Carisoprodol</td><td>Meprobamate</td><td>2-3 days</td></tr>
      <tr><td>Gabapentin</td><td>Gabapentin</td><td>1-2 days</td></tr>
      <tr class="sec"><td colspan="3">SKELETAL MUSCLE RELAXANTS</td></tr>
      <tr><td>Cyclobenzaprine</td><td>Norcyclobenzaprine</td><td>2-4 days</td></tr>
      <tr class="sec"><td colspan="3">SEDATIVES</td></tr>
      <tr><td>Zolpidem</td><td>Zolpidem acid</td><td>1-2 days</td></tr>
    </table>
  </div>
  <div class="pnum">8</div>
</section>

<section class="page odd" style="left:21px;top:504px">
  <div class="tab"><span>Tabs Here - This portion will be trimmed off</span></div>
  <div class="vtitle" style="right:13px">METABOLITES &amp; WINDOWS OF DETECTION</div>
  <div class="inner" style="right:24px">
    <table class="mtab">
      <tr><th>ANTIDEPRESSANTS</th><th>Drug or metabolite detected</th><th>Window</th></tr>
      <tr><td>Amitriptyline</td><td>Nortriptyline</td><td>2-4 days</td></tr>
      <tr><td>Citalopram</td><td>Desmethylcitalopram</td><td>2-4 days</td></tr>
      <tr><td>Duloxetine</td><td>Duloxetine</td><td>2-3 days</td></tr>
      <tr><td>Fluoxetine</td><td>Norfluoxetine</td><td>4-7 days</td></tr>
      <tr><td>Paroxetine</td><td>Paroxetine</td><td>2-3 days</td></tr>
      <tr><td>Sertraline</td><td>Norsertraline</td><td>3-5 days</td></tr>
      <tr><td>Venlafaxine</td><td>O-desmethylvenlafaxine</td><td>2-4 days</td></tr>
      <tr class="sec"><td colspan="3">ANTIPSYCHOTICS</td></tr>
      <tr><td>Aripiprazole</td><td>Dehydroaripiprazole</td><td>3-5 days</td></tr>
      <tr><td>Quetiapine</td><td>Norquetiapine</td><td>1-2 days</td></tr>
      <tr class="sec"><td colspan="3">ANTIEPILEPTICS</td></tr>
      <tr><td>Lamotrigine</td><td>Lamotrigine</td><td>2-4 days</td></tr>
      <tr class="sec"><td colspan="3">BARBITURATES</td></tr>
      <tr><td>Butalbital</td><td>Butalbital</td><td>2-4 days</td></tr>
      <tr><td>Phenobarbital</td><td>Phenobarbital</td><td>7-14 days</td></tr>
      <tr><td>Secobarbital</td><td>Secobarbital</td><td>1-2 days</td></tr>
      <tr class="sec"><td colspan="3">ALCOHOL</td></tr>
      <tr><td>Ethanol</td><td>Ethyl glucuronide</td><td>1-3 days</td></tr>
      <tr><td>Ethanol</td><td>Ethyl sulfate</td><td>1-3 days</td></tr>
      <tr class="sec"><td colspan="3">NICOTINE</td></tr>
      <tr><td>Nicotine</td><td>Cotinine</td><td>2-4 days</td></tr>
      <tr class="sec"><td colspan="3">OTHER</td></tr>
      <tr><td>Ketamine</td><td>Norketamine</td><td>1-3 days</td></tr>
      <tr><td>Naloxone</td><td>Naloxone</td><td>1 day</td></tr>
      <tr><td>Naltrexone</td><td>6-beta-naltrexol</td><td>2-3 days</td></tr>
      <tr><td>Xylazine</td><td>Xylazine</td><td>1-2 days</td></tr>
    </table>
  </div>
  <div class="pnum">9</div>
</section>

<section class="page even" style="left:195px;top:504px">
  <div class="tab"><span>Tabs Here - This portion will be trimmed off</span></div>
  <div class="inner" style="top:6px;left:15px;right:5px">
    <div class="formhead"><div class="brand" style="font-size:4.4px"><i></i>LAKESIDE LABS</div><h3>TOXICOLOGY TEST REQUISITION FORM<small>1450 Meridian Ave Suite 210, Fairview, MI 48000</small><small>(555) 014-2290 &nbsp; lakesidelabs.example</small></h3></div>
    <div class="cols box" style="grid-template-columns:1fr 1fr;margin-top:1px">
      <div><b>PATIENT INFORMATION</b><br>Last Name ______ First Name ______<br>Middle Name ___ Sex ☐M ☐F<br>Address ____________<br>City ______ State __ Zip ____<br>DOB ___/___/___ Mobile ______</div>
      <div><b>Patient Demo Attached ☐</b><br>Provider ____________<br>Collector ___________<br>Date Collected ______<br>Time Collected ______ AM/PM</div>
    </div>
    <div class="box micro" style="margin-top:1px">PRIMARY INSURANCE ☐Medicare ☐Medicaid ☐Commercial ☐Self-Pay ☐Other &nbsp; Policy # ________</div>
    <div class="box micro" style="margin-top:1px">Order Screen ☐ 12 Panel Drug Screen With Reflex Confirmation ☐ 16 Panel Drug Screen With Reflex Confirmation</div>
    <div class="box micro" style="margin-top:1px"><b>SPECIMEN INFORMATION</b> Specimen Source: ☐Urine ☐Oral Fluid &nbsp; Temperature read within 4 min ☐Yes ☐No</div>
    <div class="cols box" style="grid-template-columns:repeat(4,1fr)">
      <div><b>☐ Opiates &amp; Opioids</b><br>☐ Buprenorphine<br>☐ Codeine<br>☐ Fentanyl<br>☐ Hydrocodone<br>☐ Hydromorphone<br>☐ Meperidine<br>☐ Methadone<br>☐ Morphine<br>☐ Oxycodone<br>☐ Oxymorphone<br>☐ Tapentadol<br>☐ Tramadol<br><b>☐ Benzodiazepines</b><br>☐ Alprazolam<br>☐ Clonazepam<br>☐ Diazepam<br>☐ Lorazepam<br>☐ Temazepam</div>
      <div><b>☐ Non-Benzo Hypnotics</b><br>☐ Zolpidem<br><b>☐ Neuropathic</b><br>☐ Gabapentin<br>☐ Pregabalin<br><b>☐ Stimulants</b><br>☐ Amphetamine<br>☐ Methamphetamine<br>☐ Methylphenidate<br>☐ Phentermine<br><b>☐ Antipsychotics</b><br>☐ Aripiprazole<br>☐ Quetiapine<br>☐ Risperidone<br><b>☐ Antiepileptics</b><br>☐ Lamotrigine<br>☐ Topiramate</div>
      <div><b>☐ Antidepressants</b><br>☐ Amitriptyline<br>☐ Citalopram<br>☐ Duloxetine<br>☐ Fluoxetine<br>☐ Sertraline<br>☐ Venlafaxine<br><b>☐ Barbiturates</b><br>☐ Butalbital<br>☐ Phenobarbital<br><b>☐ Muscle Relaxants</b><br>☐ Baclofen<br>☐ Carisoprodol<br>☐ Cyclobenzaprine<br><b>☐ Illicits</b><br>☐ Cocaine<br>☐ Heroin<br>☐ MDMA</div>
      <div><b>☐ Fentanyl Analogs</b><br>☐ Acetyl Fentanyl<br>☐ Carfentanil<br>☐ Sufentanil<br><b>☐ Additional</b><br>☐ Ethyl Glucuronide<br>☐ Cotinine<br>☐ Ketamine<br>☐ Kratom<br>☐ Naloxone<br>☐ Naltrexone<br>☐ Xylazine<br>☐ THC-COOH<br>☐ ETG/ETS<br>☐ Validity</div>
    </div>
  </div>
  <div class="pnum" style="left:14px">10</div>
  <div style="position:absolute;left:11px;right:0;bottom:0;height:2px;background:var(--blue)"></div>
</section>

<section class="page odd" style="left:369px;top:504px">
  <div class="tab"><span>Tabs Here - This portion will be trimmed off</span></div>
  <div class="inner" style="left:5px;right:15px;top:6px">
    <div class="micro">ICD-10 Disclaimer: It is the sole responsibility of the ordering clinician to diagnose the patient accurately and document the codes used for medical necessity.</div>
    <div class="micro" style="margin-top:5px;font-weight:700">SUD Substance Use Disorder Patients</div>
    <div class="micro">Primary ☐ Z79.891</div>
    <div class="cols" style="grid-template-columns:1fr 1fr;margin-top:3px">
      <div><b>SUD Secondary Codes</b><br>☐ F10.11 Alcohol abuse, in remission<br>☐ F10.120 Alcohol abuse with intoxication<br>☐ F10.130 Alcohol abuse with withdrawal<br>☐ F10.20 Alcohol dependence<br>☐ F10.21 Alcohol dependence, in remission<br>☐ F11.10 Opioid abuse, uncomplicated<br>☐ F11.11 Opioid abuse, in remission<br>☐ F11.20 Opioid dependence<br>☐ F11.21 Opioid dependence, in remission<br>☐ F11.23 Opioid dependence with withdrawal<br>☐ F12.10 Cannabis abuse<br>☐ F12.20 Cannabis dependence<br>☐ F13.10 Sedative abuse<br>☐ F13.20 Sedative dependence<br>☐ F14.10 Cocaine abuse<br>☐ F14.20 Cocaine dependence</div>
      <div><b>SUD Secondary Codes</b><br>☐ F15.10 Stimulant abuse<br>☐ F15.20 Stimulant dependence<br>☐ F15.21 Stimulant dependence, in remission<br>☐ F16.10 Hallucinogen abuse<br>☐ F16.20 Hallucinogen dependence<br>☐ F18.10 Inhalant abuse<br>☐ F18.20 Inhalant dependence<br>☐ F19.10 Other substance abuse<br>☐ F19.11 Other substance abuse, in remission<br>☐ F19.20 Other substance dependence<br>☐ F19.21 Other dependence, in remission<br>☐ F19.23 Other dependence with withdrawal<br>☐ F19.94 Substance-induced mood disorder<br>☐ F19.96 Substance-induced amnestic disorder</div>
    </div>
    <div class="cols" style="grid-template-columns:1fr 1fr;margin-top:6px">
      <div><b>Provider Acknowledgement:</b><br>I acknowledge that documentation to support medical necessity for all tests ordered is recorded in the patient chart and will be made available upon request.</div>
      <div><b>Patient Consent:</b><br>I authorize release of information necessary to process claims and assign benefits to the laboratory for services performed.</div>
    </div>
    <div class="sigs micro" style="font-size:2px"><span>Provider Signature:<br>Signature Date:</span><span>Patient Signature:<br>Signature Date:</span></div>
    <div class="micro" style="display:flex;justify-content:space-between;border:.4px solid #888;padding:.5px;margin-top:4px"><span>Version Control #</span><span style="width:40%">Issue Date</span></div>
    <div style="margin-top:3px;width:36px;height:16px;background:var(--sky)"></div>
  </div>
  <div style="position:absolute;left:0;right:11px;bottom:0;height:2px;background:var(--blue)"></div>
  <div class="pnum">11</div>
</section>

<section class="page even" style="left:542px;top:504px">
  <div class="tab"><span>Tabs Here - This portion will be trimmed off</span></div>
  <div class="vtitle" style="left:13px">COMMON POC DRUG CROSS REACTANTS</div>
  <div class="inner" style="left:26px">
    <table class="mtab">
      <tr><th>SUBSTANCES THAT MAY INTERFERE</th><th>BRAND NAMES</th><th>FALSE POSITIVE RESULT</th></tr>
      <tr><td>Amantadine</td><td>Amantrel</td><td>Amphetamines</td></tr>
      <tr><td>Amitriptyline</td><td>Trilavan</td><td>Tricyclics</td></tr>
      <tr><td>Aripiprazole</td><td>Aripra</td><td>Amphetamines</td></tr>
      <tr><td>Benzphetamine</td><td>Benzora</td><td>Amphetamines</td></tr>
      <tr><td>Bupropion</td><td>Bupravex</td><td>Amphetamines</td></tr>
      <tr><td>Chlorpromazine</td><td>Chlorazine</td><td>Amphetamines</td></tr>
      <tr><td>Ciprofloxacin</td><td>Ciproxel</td><td>Opiates</td></tr>
      <tr><td>Dextromethorphan</td><td>Coughex DM</td><td>PCP, Opiates</td></tr>
      <tr><td>Diphenhydramine</td><td>Dormital</td><td>Methadone, PCP</td></tr>
      <tr><td>Doxylamine</td><td>Sleepina</td><td>Methadone</td></tr>
      <tr><td>Efavirenz</td><td>Efavira</td><td>Cannabinoids</td></tr>
      <tr><td>Ephedrine</td><td>Ephedra-X</td><td>Amphetamines</td></tr>
      <tr><td>Fluoxetine</td><td>Fluxora</td><td>Amphetamines</td></tr>
      <tr><td>Ibuprofen</td><td>Ibuvel, Painora</td><td>Cannabinoids</td></tr>
      <tr><td>Labetalol</td><td>Labetra</td><td>Amphetamines</td></tr>
      <tr><td>Levofloxacin</td><td>Levoxan</td><td>Opiates</td></tr>
      <tr><td>Metformin</td><td>Metrovia</td><td>Amphetamines</td></tr>
      <tr><td>Naproxen</td><td>Naprova</td><td>Cannabinoids</td></tr>
      <tr><td>Pantoprazole</td><td>Pantorex</td><td>Cannabinoids</td></tr>
      <tr><td>Promethazine</td><td>Promezan</td><td>Amphetamines</td></tr>
      <tr><td>Pseudoephedrine</td><td>Nasalix</td><td>Amphetamines</td></tr>
      <tr><td>Quetiapine</td><td>Quetavia</td><td>Tricyclics, Methadone</td></tr>
      <tr><td>Ranitidine</td><td>Ranitex</td><td>Amphetamines</td></tr>
      <tr><td>Rifampin</td><td>Rifamax</td><td>Opiates</td></tr>
      <tr><td>Sertraline</td><td>Sertalin</td><td>Benzodiazepines</td></tr>
      <tr><td>Tramadol</td><td>Tramora</td><td>PCP</td></tr>
      <tr><td>Trazodone</td><td>Trazolin</td><td>Amphetamines</td></tr>
      <tr><td>Venlafaxine</td><td>Venlaxor</td><td>PCP</td></tr>
      <tr><td>Verapamil</td><td>Verapra</td><td>Methadone</td></tr>
    </table>
  </div>
  <div class="pnum">12</div>
</section>

<section class="page odd cover" style="left:21px;top:714px">
  <svg viewBox="0 0 156 190" aria-hidden="true">
    <polygon points="0,0 145,0 0,68" fill="#0054AA"/>
    <polygon points="0,68 145,0 145,5 0,74" fill="#2e2e30"/>
  </svg>
  <div role="img" aria-label="Photo of a clinician in gloves drawing blood from a patient's arm" style="position:absolute;left:0;right:11px;top:50px;height:110px;background:linear-gradient(120deg,#eef0f2,#d8c8bc 45%,#b48c7e 70%,#c4c9d0);clip-path:polygon(0 32%,100% 0,100% 78%,0 100%)"></div>
  <svg viewBox="0 0 156 190" style="position:absolute;inset:0" aria-hidden="true">
    <polygon points="0,158 145,128 145,190 0,190" fill="#ffffff"/>
    <polygon points="60,190 145,150 145,190" fill="#0054AA"/>
  </svg>
  <div class="brandmark"><i></i>LAKESIDE</div>
  <div class="cover-title" style="left:33px;top:122px;font-size:9.5px;line-height:10px">Clinical<br>Laboratory</div>
  <div class="cover-title" style="left:33px;top:143px;font-size:8px;color:#444;letter-spacing:.5px">SERVICES</div>
  <div class="tab"><span style="opacity:.5">Clinical Laboratory Services</span></div>
  <div class="pnum" style="color:#fff">13</div>
</section>

<section class="page even" style="left:195px;top:714px">
  <div class="tab"><span>Tabs Here - This portion will be trimmed off</span></div>
  <div class="pnum">14</div>
</section>

<section class="page odd" style="left:369px;top:714px">
  <div class="tab"><span>Tabs Here - This portion will be trimmed off</span></div>
  <div class="inner" style="left:5px;right:15px;top:6px">
    <div class="formhead"><div class="brand" style="font-size:4.4px"><i></i>LAKESIDE LABS</div><h3>BLOOD TEST REQUISITION FORM<small>1450 Meridian Ave Suite 210, Fairview, MI 48000</small><small>(555) 014-2290 &nbsp; lakesidelabs.example</small></h3></div>
    <div class="cols box" style="grid-template-columns:1fr 1fr;margin-top:1px">
      <div><b>PATIENT INFORMATION</b><br>Last Name ______ First Name ____<br>Sex ☐M ☐F &nbsp; DOB ___/___/___<br>Address ___________<br>City _____ State __ Zip ___</div>
      <div><b>Provider:</b><br>Specimen Information<br>☐Urine ☐Blood ☐Swab ☐Other<br>Date Collected ____ Time ____</div>
    </div>
    <div class="box micro" style="margin-top:1px">INSURANCE INFORMATION ☐Commercial ☐Medicare ☐Medicaid ☐Self-Pay ☐Bill to Client</div>
    <div class="band" style="font-size:2px">PLEASE MARK THE DESIRED TEST(S) OR PANELS TO BE TESTED</div>
    <div class="cols box" style="grid-template-columns:repeat(4,1fr)">
      <div><b>PANELS</b><br>☐ Basic Metabolic<br>☐ Comprehensive Metabolic<br>☐ Hepatic Function<br>☐ Lipid Panel<br>☐ Renal Panel<br><b>CHEMISTRY</b><br>☐ Albumin<br>☐ ALT<br>☐ AST<br>☐ Bilirubin<br>☐ BUN<br>☐ Calcium<br>☐ Chloride<br>☐ CO2<br>☐ Creatinine<br>☐ Glucose<br>☐ Magnesium<br>☐ Phosphorus<br>☐ Potassium<br>☐ Sodium<br>☐ Uric Acid</div>
      <div><b>CHEMISTRY (cont)</b><br>☐ Amylase<br>☐ CK<br>☐ Ferritin<br>☐ Folate<br>☐ GGT<br>☐ Iron<br>☐ LDH<br>☐ Lipase<br>☐ TIBC<br>☐ Vitamin B12<br>☐ Vitamin D<br><b>HEMATOLOGY</b><br>☐ CBC w/ Diff<br>☐ CBC w/o Diff<br>☐ ESR<br>☐ Reticulocyte<br>☐ PT/INR<br>☐ PTT<br>☐ Fibrinogen<br>☐ D-Dimer</div>
      <div><b>ENDOCRINE</b><br>☐ TSH<br>☐ Free T4<br>☐ Free T3<br>☐ Hemoglobin A1c<br>☐ Insulin<br>☐ Cortisol<br>☐ Estradiol<br>☐ FSH<br>☐ LH<br>☐ Testosterone<br>☐ PSA<br>☐ hCG<br><b>IMMUNOLOGY</b><br>☐ ANA<br>☐ CRP<br>☐ hs-CRP<br>☐ RF<br>☐ ASO</div>
      <div><b>SEROLOGY</b><br>☐ Hepatitis A<br>☐ Hepatitis B<br>☐ Hepatitis C<br>☐ HIV 1/2<br>☐ RPR<br>☐ Lyme<br><b>URINALYSIS</b><br>☐ UA Complete<br>☐ UA w/ Reflex<br>☐ Microalbumin<br><b>BLOOD BANK</b><br>☐ ABO/Rh<br>☐ Antibody Screen<br><b>ALLERGY</b><br>☐ Food Panel<br>☐ Inhalant Panel</div>
    </div>
  </div>
  <div class="pnum">15</div>
</section>

<section class="page even" style="left:542px;top:714px">
  <div class="tab"><span>Tabs Here - This portion will be trimmed off</span></div>
  <div class="inner" style="top:5px;left:16px;right:5px">
    <div class="band" style="margin-top:0">DIAGNOSIS (ICD-10) INFORMATION</div>
    <div class="sub">BASIC METABOLIC PANEL</div>
    <div class="cols" style="grid-template-columns:repeat(3,1fr);margin-top:0"><div>☐ E11.9 Type 2 diabetes<br>☐ E78.5 Hyperlipidemia<br>☐ I10 Hypertension</div><div>☐ N18.3 CKD stage 3<br>☐ E87.1 Hyponatremia<br>☐ E87.6 Hypokalemia</div><div>☐ R73.03 Prediabetes<br>☐ Z79.899 Long-term drug use<br>☐ R53.83 Fatigue</div></div>
    <div class="sub">COMPLETE BLOOD COUNT</div>
    <div class="cols" style="grid-template-columns:repeat(3,1fr);margin-top:0"><div>☐ D64.9 Anemia<br>☐ D50.9 Iron deficiency<br>☐ D69.6 Thrombocytopenia</div><div>☐ R50.9 Fever<br>☐ D72.829 Leukocytosis<br>☐ R58 Hemorrhage</div><div>☐ Z01.812 Pre-procedure labs<br>☐ R53.81 Malaise<br>☐ Z00.00 General exam</div></div>
    <div class="sub">HEPATIC FUNCTION PANEL</div>
    <div class="cols" style="grid-template-columns:repeat(3,1fr);margin-top:0"><div>☐ K76.0 Fatty liver<br>☐ K70.30 Alcoholic cirrhosis<br>☐ R74.01 Elevated LFTs</div><div>☐ K75.9 Hepatitis<br>☐ R17 Jaundice<br>☐ K74.60 Cirrhosis</div><div>☐ B18.2 Chronic hep C<br>☐ Z79.891 Opioid therapy<br>☐ R10.9 Abdominal pain</div></div>
    <div class="sub">ACUTE HEPATITIS PANEL</div>
    <div class="cols" style="grid-template-columns:repeat(3,1fr);margin-top:0"><div>☐ B15.9 Hepatitis A<br>☐ B16.9 Hepatitis B</div><div>☐ B17.10 Hepatitis C<br>☐ Z20.5 Exposure</div><div>☐ F11.20 Opioid dependence<br>☐ Z72.89 Risk behavior</div></div>
    <div class="sub">LIPID &amp; CHOLESTEROL</div>
    <div class="cols" style="grid-template-columns:repeat(3,1fr);margin-top:0"><div>☐ E78.00 Hypercholesterolemia<br>☐ E78.1 Hypertriglyceridemia</div><div>☐ I25.10 Coronary disease<br>☐ Z82.49 Family history</div><div>☐ E66.9 Obesity<br>☐ Z13.220 Lipid screening</div></div>
    <div class="sub">THYROID PANEL</div>
    <div class="cols" style="grid-template-columns:repeat(3,1fr);margin-top:0"><div>☐ E03.9 Hypothyroidism<br>☐ E05.90 Hyperthyroidism</div><div>☐ E04.2 Thyroid nodules<br>☐ R63.5 Weight gain</div><div>☐ E06.3 Thyroiditis<br>☐ R00.2 Palpitations</div></div>
    <div class="sub">URINALYSIS</div>
    <div class="cols" style="grid-template-columns:repeat(3,1fr);margin-top:0"><div>☐ N39.0 UTI<br>☐ R31.9 Hematuria</div><div>☐ R80.9 Proteinuria<br>☐ R30.0 Dysuria</div><div>☐ N20.0 Kidney stone<br>☐ R35.0 Frequency</div></div>
    <div class="sub">OTHER</div>
    <div class="micro" style="font-weight:700;margin-top:3px">PATIENT AUTHORIZATION</div>
    <div class="micro">I authorize the release of medical information needed to process claims and assign payment of benefits to the laboratory.</div>
    <div class="micro" style="font-weight:700;margin-top:2px">AUTHORIZED HEALTHCARE PROVIDER ACKNOWLEDGEMENT</div>
    <div class="micro">Documentation supporting medical necessity is recorded in the patient chart.</div>
  </div>
  <div class="pnum">16</div>
</section>

<section class="page odd report" style="left:21px;top:924px">
  <div class="tab"><span>Tabs Here - This portion will be trimmed off</span></div>
  <div class="inner">
    <div class="final">PRELIMINARY</div>
    <div class="rhead"><div class="brand"><i></i>LAKESIDE LABS</div><div class="micro">1450 Meridian Ave, Suite 210<br>(555) 014-2290</div><div class="micro">LAB DIRECTOR Daniel Reyes, MD<br>CLIA ID# 00D0000000</div></div>
    <div class="rule"></div>
    <div class="micro">XXX, XXX &nbsp; Patient #: XXX &nbsp; DOB: XXX &nbsp; Accession: XXX<br>Organization: Lakeview Internal Medicine</div>
    <div class="rtitle">LL Blood Profiles</div>
    <table><tr><th>Test Name</th><th>Result</th><th>Units</th><th>Flag</th><th>Reference Range</th></tr>
    <tr><td><b>CBC W/ DIFF</b></td><td></td><td></td><td></td><td></td></tr>
    <tr><td>WBC Count</td><td>4.5</td><td>10^3 cells/uL</td><td></td><td>3.8 - 10.8</td></tr>
    <tr><td>RBC Count</td><td>4.26</td><td>10^6 cells/uL</td><td></td><td>4.20 - 5.80</td></tr>
    <tr><td>Hemoglobin</td><td>11.0</td><td>g/dL</td><td class="neg">LOW</td><td>13.2 - 17.1</td></tr>
    <tr><td>Hematocrit</td><td>33.6</td><td>%</td><td class="neg">LOW</td><td>38.5 - 50.0</td></tr>
    <tr><td>MCV</td><td>79.0</td><td>fL</td><td class="neg">LOW</td><td>80.0 - 100.0</td></tr>
    <tr><td>MCH</td><td>25.9</td><td>pg</td><td class="neg">LOW</td><td>27.0 - 33.0</td></tr>
    <tr><td>MCHC</td><td>32.7</td><td>g/dL</td><td></td><td>32.0 - 36.0</td></tr>
    <tr><td>RDW</td><td>15.1</td><td>%</td><td></td><td>11.0 - 15.0</td></tr>
    <tr><td>Platelet Count</td><td>263</td><td>10^3 cells/uL</td><td></td><td>140 - 400</td></tr>
    <tr><td>MPV</td><td>9.5</td><td>fL</td><td></td><td>7.5 - 12.5</td></tr>
    <tr><td>Neutrophils %</td><td>57</td><td>%</td><td></td><td>40 - 74</td></tr>
    <tr><td>Lymphocytes %</td><td>31</td><td>%</td><td></td><td>19 - 48</td></tr>
    <tr><td>Monocytes %</td><td>8</td><td>%</td><td></td><td>3 - 12</td></tr>
    <tr><td>Eosinophils %</td><td>3</td><td>%</td><td></td><td>0 - 7</td></tr>
    <tr><td>Basophils %</td><td>1</td><td>%</td><td></td><td>0 - 2</td></tr>
    <tr><td>Neutrophils Abs</td><td>2.57</td><td>10^3 cells/uL</td><td></td><td>1.50 - 7.80</td></tr>
    <tr><td>Lymphocytes Abs</td><td>1.40</td><td>10^3 cells/uL</td><td></td><td>0.85 - 3.90</td></tr>
    <tr><td>NRBC %</td><td>0</td><td>%</td><td></td><td>0 - 0</td></tr></table>
    <div class="rfoot"><span>Printed: 11/21/2025<br>Page: 1/2</span><span>STAT(S) Corrected (C) Amended (A)</span><span>Lab Results for: XXX</span></div>
  </div>
  <div class="pnum">17</div>
</section>

<section class="page even report" style="left:195px;top:924px">
  <div class="tab"><span>Tabs Here - This portion will be trimmed off</span></div>
  <div class="inner">
    <div class="final">PRELIMINARY</div>
    <div class="rhead"><div class="brand"><i></i>LAKESIDE LABS</div><div class="micro">1450 Meridian Ave, Suite 210<br>(555) 014-2290</div><div class="micro">LAB DIRECTOR Daniel Reyes, MD<br>CLIA ID# 00D0000000</div></div>
    <div class="rule"></div>
    <div class="micro">XXX, XXX &nbsp; Patient #: XXX &nbsp; DOB: XXX &nbsp; Accession: XXX</div>
    <div class="rtitle">LL Blood Profiles</div>
    <table><tr><th>Test Name</th><th>Result</th><th>Units</th><th>Flag</th><th>Reference Range</th></tr>
    <tr><td><b>Comprehensive Metabolic Panel</b></td><td></td><td></td><td></td><td></td></tr>
    <tr><td>A/G Ratio</td><td>1.5</td><td></td><td></td><td>0.9 - 1.8</td></tr>
    <tr><td>ALT (SGPT)</td><td>15</td><td>U/L</td><td></td><td>10 - 49</td></tr>
    <tr><td>Albumin</td><td>3.9</td><td>g/dL</td><td></td><td>3.2 - 4.8</td></tr>
    <tr><td>Alkaline Phosphatase</td><td>80</td><td>U/L</td><td></td><td>46 - 116</td></tr>
    <tr><td>AST (SGOT)</td><td>19</td><td>U/L</td><td></td><td>0 - 34</td></tr>
    <tr><td>Calcium</td><td>8.9</td><td>mg/dL</td><td></td><td>8.7 - 10.4</td></tr>
    <tr><td>Carbon Dioxide</td><td>26</td><td>mmol/L</td><td></td><td>20 - 31</td></tr>
    <tr><td>Chloride</td><td>103</td><td>mmol/L</td><td></td><td>98 - 107</td></tr>
    <tr><td>Creatinine</td><td>0.80</td><td>mg/dL</td><td></td><td>0.55 - 1.02</td></tr>
    <tr><td>Globulin</td><td>2.6</td><td>g/dL</td><td></td><td>2.0 - 3.5</td></tr>
    <tr><td>Glucose</td><td>98</td><td>mg/dL</td><td></td><td>74 - 106</td></tr>
    <tr><td>Potassium</td><td>4.3</td><td>mmol/L</td><td></td><td>3.5 - 5.1</td></tr>
    <tr><td>Sodium</td><td>139</td><td>mmol/L</td><td></td><td>136 - 145</td></tr>
    <tr><td>Total Protein</td><td>6.5</td><td>g/dL</td><td class="neg">LOW</td><td>6.6 - 8.3</td></tr>
    <tr><td>Urea Nitrogen</td><td>14</td><td>mg/dL</td><td></td><td>9 - 23</td></tr>
    <tr><td><b>THYROID PANEL</b></td><td></td><td></td><td></td><td></td></tr>
    <tr><td>Free T3</td><td>2.98</td><td>pg/mL</td><td></td><td>2.30 - 4.20</td></tr>
    <tr><td>Free T4</td><td>0.90</td><td>ng/dL</td><td></td><td>0.89 - 1.76</td></tr>
    <tr><td>TSH</td><td>1.954</td><td>uIU/mL</td><td></td><td>0.550 - 4.780</td></tr>
    <tr><td><b>Partner Lab Blood Tests</b></td><td></td><td></td><td></td><td></td></tr>
    <tr><td>Cyclic Citrullinated Peptide</td><td>Pending</td><td></td><td></td><td></td></tr>
    <tr><td>Thyroid Peroxidase</td><td>Pending</td><td></td><td></td><td></td></tr>
    <tr><td>ANA IFA Profile</td><td>Pending</td><td></td><td></td><td></td></tr></table>
    <div class="rfoot"><span>Printed: 11/21/2025<br>Page: 2/2</span><span>STAT(S) Corrected (C) Amended (A)</span><span>Lab Results for: XXX</span></div>
  </div>
  <div class="pnum">18</div>
</section>

<section class="page odd critical" style="left:369px;top:924px">
  <div class="tab"><span>Tabs Here - This portion will be trimmed off</span></div>
  <div class="inner" style="left:8px;right:20px;top:6px">
    <h2>PHYSICIAN NOTIFICATIONS OF CRITICAL VALUES</h2>
    <div class="micro" style="text-align:center;margin-top:1px">The following test results are to result in the immediate notification of the physician:</div>
    <div class="band">CHEMISTRY CRITICAL VALUES</div>
    <table>
      <tr><td>TEST NAME</td><td>LESS THAN</td><td>GREATER THAN</td></tr>
      <tr><td>B-type Natriuretic Peptide</td><td></td><td>400</td></tr>
      <tr><td>CALCIUM [CA]</td><td>7</td><td>12.9</td></tr>
      <tr><td>CARBON DIOXIDE [ECO2]</td><td>10</td><td>40</td></tr>
      <tr><td>Creatinine [CREZS]</td><td></td><td>5</td></tr>
      <tr><td>Glucose [GLUC]</td><td>50</td><td>400</td></tr>
      <tr><td>MAGNESIUM [MG]</td><td>1</td><td>4</td></tr>
      <tr><td>PHOSPHORUS [PHOS]</td><td>1.2</td><td>8</td></tr>
      <tr><td>Potassium [K]</td><td>2.8</td><td>6</td></tr>
      <tr><td>SODIUM [NA]</td><td>124</td><td>154</td></tr>
      <tr><td>TRIGLYCERIDES [TGL]</td><td></td><td>500</td></tr>
      <tr><td>UREA NITROGEN [BUN]</td><td></td><td>100</td></tr>
    </table>
    <div class="band">TOXIC VALUES-THERAPEUTIC DRUG MONITORING</div>
    <table>
      <tr><td>TEST NAME</td><td>LESS THAN</td><td>GREATER THAN</td></tr>
      <tr><td>HEMOGLOBIN [HGB]</td><td>6</td><td>20</td></tr>
      <tr><td>HEMATOCRIT [HCT]</td><td>20</td><td>65</td></tr>
      <tr><td>PLATELET COUNT [PLT]</td><td>50</td><td>1000</td></tr>
      <tr><td>INTERNATIONAL NORMALIZED RATIO</td><td></td><td>5</td></tr>
      <tr><td>Activated Partial Thromboplastin Time</td><td></td><td>129</td></tr>
      <tr><td>WBC COUNT</td><td>2</td><td>50</td></tr>
    </table>
    <div class="band">TOXIC VALUES-THERAPEUTIC DRUG MONITORING</div>
    <table>
      <tr><td>TEST NAME</td><td>LESS THAN</td><td>GREATER THAN</td></tr>
      <tr><td>Carbamazepine [CBM]</td><td></td><td>20</td></tr>
      <tr><td>Digoxin [DIGN]</td><td></td><td>2.5</td></tr>
      <tr><td>Lithium [LI]</td><td></td><td>2</td></tr>
      <tr><td>Phenobarbital [PHNO]</td><td></td><td>60</td></tr>
      <tr><td>PHENYTOIN [PTN]</td><td></td><td>30</td></tr>
      <tr><td>VALPROIC ACID [VALP]</td><td></td><td>150</td></tr>
    </table>
    <div class="micro" style="margin-top:3px">PROCEDURE: The following items will be recorded in the Notification of Physician of Critical Values Record: the person placing the call, details of the call, the result given and the time/date the result was given. If no answer is received, an attempt to contact a physician will be repeated every hour until the results have been given.</div>
  </div>
  <div style="position:absolute;left:0;right:11px;bottom:0;height:2px;background:var(--blue)"></div>
  <div class="pnum">19</div>
</section>

<section class="page even" style="left:542px;top:924px">
  <div class="tab"><span>Tabs Here - This portion will be trimmed off</span></div>
  <div class="pnum">20</div>
</section>

</body>
</html>
```